Brisk Coatings business card for residential and commercial painting

A clean, professional design. Easy to read
Eye catching and elegant
Front could have some color variations
On the back of card I would like all black with signature logo

*Attached is my current business card and the items I want displayed

Contact Information for Business Card

Email, phone number, website, and owner name

Font styles to use
Serif

Requirements
Must have
• My logo with cool design and perhaps some paint splatter

```html
<!DOCTYPE html>
<html lang="en">
<head>
<meta charset="utf-8">
<title>Brisk Coatings – Business Card</title>
<link href="https://fonts.googleapis.com/css2?family=Oswald:wght@400;500&family=Arimo:wght@400&display=swap" rel="stylesheet">
<style>
  :root {
    --stage: #1b1b1b;
    --paper: #ffffff;
    --brand-blue: #1075be;
    --ink: #2b2b2b;
    --slate: #3a3a3c;
    --rule: #d6d6d6;
  }
  * { margin: 0; padding: 0; box-sizing: border-box; }
  html, body {
    width: 1200px; height: 801px; overflow: hidden;
    background: var(--stage);
  }
  .card {
    position: absolute; top: 274px;
    width: 443px; height: 263px;
    box-shadow: 2px 2px 3px rgba(0,0,0,.6);
    overflow: hidden;
  }
  .card--front { left: 153px; background: var(--paper); }
  .card--back { left: 625px; background: var(--brand-blue); }

  .wordmark {
    position: absolute;
    font-family: "Oswald", sans-serif;
    font-weight: 500;
    white-space: nowrap;
    line-height: 1;
  }
  .card--front .wordmark {
    left: 20px; width: 190px; top: 117px;
    text-align: center;
    font-size: 26px; color: var(--brand-blue);
  }
  .card--back .wordmark {
    left: 178px; top: 75px;
    font-size: 33px; color: var(--paper);
  }

  .divider {
    position: absolute; left: 225px; top: 48px;
    width: 1px; height: 175px;
    background: linear-gradient(to bottom, transparent, var(--rule) 15%, var(--rule) 85%, transparent);
  }

  .owner {
    position: absolute; left: 240px; top: 60px;
  }
  .owner__name {
    font-family: "Oswald", sans-serif; font-weight: 400;
    font-size: 23px; color: var(--brand-blue); line-height: 1.05;
  }
  .owner__title {
    font-family: "Arimo", sans-serif;
    font-size: 12.5px; color: var(--ink); margin-top: 1px;
  }

  .contacts {
    position: absolute; left: 240px; top: 121px;
    list-style: none;
    font-family: "Arimo", sans-serif; font-size: 12.5px; color: var(--ink);
  }
  .contacts li {
    display: flex; align-items: center; height: 15.6px;
  }
  .contacts svg { width: 13px; height: 13px; margin-right: 8px; flex: none; }
  .contacts .accent { color: var(--brand-blue); }

  .slate-band {
    position: absolute; left: 0; top: 0;
    width: 118px; height: 100%;
    background: var(--slate);
  }

  .price {
    position: absolute; left: 210px; top: 213px;
    display: flex; align-items: center; gap: 5px;
    font-family: "Oswald", sans-serif; font-size: 14px; color: var(--paper);
  }
  .price__field {
    width: 49px; height: 18px; border-radius: 9px; background: var(--paper);
  }
</style>
</head>
<body>

<section class="card card--front" aria-label="Card front">
  <div class="wordmark">BRISK COATINGS</div>
  <div class="divider"></div>
  <div class="owner">
    <div class="owner__name">Marcus "Mack"</div>
    <div class="owner__title">Owner-Licensed &amp; Insured</div>
  </div>
  <ul class="contacts">
    <li>
      <svg viewBox="0 0 16 16" aria-hidden="true"><path fill="#1075be" d="M3.6 1.5l2.3 2.6-1.3 1.7c.9 2 2.4 3.6 4.4 4.6l1.7-1.4 2.7 2.3-1.3 2.3C7.5 13.4 2.7 8.6 1.5 3z"/><path d="M9.5 2.2a4.6 4.6 0 0 1 4.3 4.3M9.3 4.6a2.2 2.2 0 0 1 2.1 2" stroke="#1075be" stroke-width="1.3" fill="none"/></svg>
      93.555.0147
    </li>
    <li>
      <svg viewBox="0 0 16 16" aria-hidden="true"><rect x="1" y="3.5" width="14" height="9" fill="#1075be"/><path d="M1 3.5l7 5 7-5M1 12.5l5-4.2M15 12.5l-5-4.2" stroke="#fff" stroke-width="1" fill="none"/></svg>
      briskcoatingstn@mail.com
    </li>
    <li>
      <svg viewBox="0 0 16 16" aria-hidden="true"><g stroke="#1075be" stroke-width="1.2" fill="none"><circle cx="8" cy="8" r="6.5"/><ellipse cx="8" cy="8" rx="2.8" ry="6.5"/><path d="M1.5 8h13M2.6 4.8h10.8M2.6 11.2h10.8"/></g></svg>
      <span>www.<span class="accent">briskcoatingstn</span>.com</span>
    </li>
  </ul>
</section>

<section class="card card--back" aria-label="Card back">
  <div class="slate-band"></div>
  <div class="wordmark">BRISK COATINGS</div>
  <div class="price">
    <span>Price</span>
    <span class="price__field"></span>
  </div>
</section>

</body>
</html>
```